Business Card Design Project

We are not a new company, but renamed to "Vantorin Kitchens" last year. We specialize in modern high-end cabinetry imports. We would like to communicate a sense of quality and cutting edge technology. Ideally the design would incorporate our logo colors, silver, red and preferably a black, matte background. Though we are open to suggestions.
Logo is attached.
Edit: I have attached rough drafts of the previous cards, this way you will have all necessary content that needs to go on the cards.
Updates
Project Deadline Extended
Reason: We have received a lot of great designs, but due to the sheer number we couldn't respond to all. We will extend the deadline for another 7 days to finalize and provide feedback to designers.
Thank you for your hard work!
Industry/Entity Type
Business
Look and feel
Each slider illustrates characteristics of the customer's brand and the style your logo design should communicate.

```html
<!DOCTYPE html>
<html lang="en">
<head>
<meta charset="utf-8">
<title>Vantorin Kitchens – Business Cards</title>
<link rel="stylesheet" href="https://fonts.googleapis.com/css2?family=Exo+2:wght@400;500&display=swap">
<style>
  :root {
    --backdrop: #5c5c5c;
    --card: #2a2a2a;
    --silver: #d2d2d2;
    --silver-dark: #a9a9a9;
    --red: #e32129;
    --text: #e6e6e6;
    --shadow: rgba(0, 0, 0, 0.45);
  }
  * { margin: 0; padding: 0; box-sizing: border-box; }
  html, body {
    width: 1200px;
    height: 900px;
    overflow: hidden;
    background: var(--backdrop);
    font-family: "Exo 2", Arial, sans-serif;
  }
  .canvas {
    position: relative;
    width: 1200px;
    height: 900px;
  }
  .card {
    position: absolute;
    width: 600px;
    height: 343px;
    background: var(--card);
    box-shadow: 0 14px 30px var(--shadow);
    overflow: hidden;
  }
  .card--front { left: 140px; top: 80px; }
  .card--back  { left: 460px; top: 480px; }

  .card__bands {
    position: absolute;
    left: 0;
    right: 0;
    bottom: 0;
  }
  .band-silver {
    height: 9px;
    background: linear-gradient(180deg, #f0f0f0, var(--silver-dark));
  }
  .band-gap { height: 3px; background: #1e1e1e; }
  .band-red { height: 24px; background: var(--red); }

  /* Front */
  .brand {
    position: absolute;
    display: flex;
    align-items: center;
    gap: 16px;
    color: var(--silver);
    font-weight: 500;
    letter-spacing: 0.06em;
    text-transform: uppercase;
  }
  .brand__mark {
    width: 26px;
    height: 26px;
    background: var(--silver);
    flex: none;
  }
  .card--front .brand {
    left: 0;
    right: 0;
    top: 132px;
    justify-content: center;
    font-size: 38px;
  }

  /* Back */
  .card--back .brand {
    left: 40px;
    top: 128px;
    font-size: 19px;
    line-height: 1.25;
    gap: 12px;
  }
  .card--back .brand__mark { width: 20px; height: 20px; }

  .contact {
    position: absolute;
    left: 290px;
    top: 38px;
    color: var(--text);
  }
  .contact__name {
    font-size: 22px;
    font-weight: 400;
    letter-spacing: 0.03em;
    text-transform: uppercase;
  }
  .contact__role {
    font-size: 13px;
    margin-left: 4px;
    text-transform: none;
    letter-spacing: 0.02em;
  }
  .contact__lines {
    list-style: none;
    margin-top: 22px;
    font-size: 15px;
    line-height: 18px;
    letter-spacing: 0.04em;
  }
  .contact__label {
    display: inline-block;
    width: 18px;
    color: var(--red);
  }
  .contact__address {
    margin-top: 20px;
    font-size: 15px;
    letter-spacing: 0.02em;
  }
  .contact__web {
    margin-top: 18px;
    font-size: 16px;
    color: var(--red);
    letter-spacing: 0.08em;
  }
</style>
</head>
<body>
<main class="canvas">

  <section class="card card--front" aria-label="Business card front">
    <div class="brand">
      <span class="brand__mark"></span>
      <span class="brand__name">Vantorin Kitchens</span>
    </div>
    <div class="card__bands">
      <div class="band-silver"></div>
      <div class="band-gap"></div>
      <div class="band-red"></div>
    </div>
  </section>

  <section class="card card--back" aria-label="Business card back">
    <div class="brand">
      <span class="brand__mark"></span>
      <span class="brand__name">Vantorin<br>Kitchens</span>
    </div>

    <div class="contact">
      <h1 class="contact__name">Daniel Morrow<span class="contact__role">| Director</span></h1>
      <ul class="contact__lines">
        <li><span class="contact__label">P</span>780.555.0142</li>
        <li><span class="contact__label">F</span>780.555.0187</li>
        <li><span class="contact__label">C</span>780.555.0163</li>
        <li>daniel@vantorinkitchens.ca</li>
      </ul>
      <p class="contact__address">4512 - 76 Ave., Edmonton, AB T6B 2K9</p>
      <p class="contact__web">vantorinkitchens.ca</p>
    </div>

    <div class="card__bands">
      <div class="band-silver"></div>
      <div class="band-gap"></div>
      <div class="band-red"></div>
    </div>
  </section>

</main>
</body>
</html>
```